Event flyer for Sunday night Youth Group

Need a 4 x 6 or 5 x 7 flyer for a new youth group starting on April 14. The youth group is for students in middle school and high school so it needs to look fun and cool, but not childish. I prefer it not to include pictures of people unless it's so obscure you can't really see their faces. I've uploaded some pictures of flyers I like. I've also attached a couple versions of our logo to use on the flyer.
Information the flyer needs to include:
Youth Group
Sundays, 6-8pm (beginning April 14)
Location: Marlowe's - 4219 Quarry Fern Ave N, Keizer, 97318
There will be dinner, games, friends, and a message.
Target Market(s)
Youth ages 13-18
Industry/Entity Type
Church
Font styles to use
Colors
Designer to choose colors to be used in the design.
Look and feel

```html
<!DOCTYPE html>
<html lang="en">
<head>
<meta charset="utf-8">
<title>Youth Group – Sunday Nights Flyer</title>
<link rel="stylesheet" href="https://fonts.googleapis.com/css2?family=Montserrat:wght@400;500;600;700;800&family=Playball&family=Oswald:wght@700&family=Fira+Sans:wght@600;700&display=swap">
<style>
  :root {
    --navy-deep: #06161f;
    --navy: #133646;
    --brown: #5a3214;
    --brown-dark: #3d230f;
    --rust: #a4521a;
    --gold: #d9c577;
    --sage: #7f9484;
    --paper: #f1f0ee;
    --page: #ffffff;
    --ink: #1b1b1b;
  }
  * { margin: 0; padding: 0; box-sizing: border-box; }
  html, body { width: 1200px; height: 2823px; overflow: hidden; background: var(--page); }
  .stage { position: relative; width: 1200px; height: 2823px; }
  .flyer {
    position: absolute; left: 50px; top: 640px;
    width: 872px; height: 1220px;
    transform: scale(1.2615); transform-origin: top left;
    background: var(--paper);
    overflow: hidden;
    box-shadow: 0 20px 40px rgba(0,0,0,.25);
  }
  .backdrop { position: absolute; left: 0; top: 0; width: 872px; height: 780px; }
  .brand {
    position: absolute; top: 78px; left: 0; width: 872px;
    display: flex; justify-content: center; align-items: center; gap: 22px;
  }
  .brand-mark { width: 38px; height: 38px; background: var(--sage); }
  .brand-name {
    font-family: "Montserrat", sans-serif; font-weight: 500;
    font-size: 40px; letter-spacing: 4px; color: var(--sage); line-height: 1;
  }
  .badge { position: absolute; left: 182px; top: 182px; width: 510px; height: 510px; }
  .badge-title {
    position: absolute; left: 182px; top: 182px; width: 510px; height: 510px;
    display: flex; flex-direction: column; align-items: center; justify-content: center;
  }
  .title-script {
    font-family: "Playball", cursive; font-size: 118px; color: var(--rust);
    line-height: .9; margin-left: -10px; margin-top: -10px;
    text-shadow: 0 3px 4px rgba(0,0,0,.25);
  }
  .title-block {
    font-family: "Oswald", sans-serif; font-weight: 700; font-size: 104px;
    line-height: 1; letter-spacing: 1px;
    background: linear-gradient(90deg, #4a1620 0%, #2d2430 45%, var(--navy) 100%);
    -webkit-background-clip: text; background-clip: text; color: transparent;
    filter: drop-shadow(0 4px 4px rgba(0,0,0,.3));
  }
  .schedule {
    position: absolute; top: 745px; width: 872px; text-align: center;
    font-family: "Montserrat", sans-serif; font-weight: 800; font-size: 64px;
    line-height: 1; color: var(--brown);
  }
  .schedule .time { color: var(--navy); }
  .start-tab {
    position: absolute; top: 832px; left: 290px; width: 292px; height: 52px;
    background: var(--navy); border-radius: 10px 10px 0 0;
    font-family: "Montserrat", sans-serif; font-weight: 500; font-size: 33px;
    color: #fff; text-align: center; line-height: 52px; letter-spacing: 1px;
  }
  .start-date {
    position: absolute; top: 880px; left: 214px; width: 444px; height: 92px;
    display: flex; border-radius: 18px; overflow: hidden;
  }
  .start-day {
    width: 222px; background: var(--navy); color: #fff;
    font-family: "Montserrat", sans-serif; font-weight: 800; font-size: 70px;
    display: flex; align-items: center; justify-content: center; line-height: 1;
  }
  .start-day sup { font-size: 30px; margin-left: 2px; align-self: flex-start; margin-top: 14px; }
  .start-month {
    flex: 1; background: var(--brown); color: #fff; border-radius: 18px;
    font-family: "Montserrat", sans-serif; font-weight: 800; font-size: 54px;
    display: flex; align-items: center; justify-content: center; letter-spacing: -1px;
  }
  .location-label {
    position: absolute; top: 990px; left: 0; width: 872px; text-align: center;
    font-family: "Montserrat", sans-serif; font-weight: 700; font-size: 20px;
    letter-spacing: 6px; color: var(--ink);
  }
  .location-label span { background: var(--paper); padding: 0 6px; }
  .location-box {
    position: absolute; top: 1006px; left: 86px; width: 701px; height: 56px;
    border: 2px solid var(--rust);
    font-family: "Fira Sans", sans-serif; font-weight: 600; font-size: 27px;
    color: var(--brown); display: flex; align-items: center; justify-content: center;
  }
  .location-box .venue { color: var(--rust); margin-right: 6px; }
  .extras-label {
    position: absolute; top: 1082px; width: 872px; text-align: center;
    font-family: "Montserrat", sans-serif; font-weight: 700; font-size: 17px;
    letter-spacing: 2px; color: var(--ink);
  }
  .extras {
    position: absolute; top: 1110px; width: 872px;
    display: flex; justify-content: center; list-style: none;
    font-family: "Fira Sans", sans-serif; font-weight: 700; font-size: 22px;
  }
  .extras li { padding: 6px 22px; border-left: 2px solid var(--ink); line-height: 1.6; }
  .extras li:first-child { border-left: none; }
  .extras .navy { color: var(--navy); }
  .extras .brown { color: var(--brown); }
</style>
</head>
<body>
<div class="stage">
  <article class="flyer">
    <svg class="backdrop" viewBox="0 0 872 780" role="img" aria-label="Dark backdrop with faint raised hands fading into a brown brush stroke">
      <defs>
        <linearGradient id="dusk" x1="0" y1="0" x2="0" y2="1">
          <stop offset="0" stop-color="#04141c"/>
          <stop offset=".45" stop-color="#12262e"/>
          <stop offset=".75" stop-color="#3a2614"/>
          <stop offset="1" stop-color="#4b2d12"/>
        </linearGradient>
      </defs>
      <path d="M0 0 H872 V420 L860 470 L800 540 L720 610 L640 660 L560 700 L470 740 L380 760 L300 745 L220 715 L140 680 L60 640 L0 610 V520 L40 470 L0 450 Z" fill="url(#dusk)"/>
    </svg>

    <header class="brand">
      <span class="brand-mark"></span>
      <span class="brand-name">HARBORLIGHT FELLOWSHIP</span>
    </header>

    <svg class="badge" viewBox="0 0 510 510" aria-hidden="true">
      <defs>
        <linearGradient id="ring" x1="0" y1="0" x2="1" y2="1">
          <stop offset="0" stop-color="#8a7a3a"/>
          <stop offset=".5" stop-color="#f0e2a0"/>
          <stop offset="1" stop-color="#8a7a3a"/>
        </linearGradient>
        <radialGradient id="disc" cx=".45" cy=".4" r=".65">
          <stop offset="0" stop-color="#ffffff"/>
          <stop offset="1" stop-color="#e2e0e0"/>
        </radialGradient>
      </defs>
      <circle cx="255" cy="255" r="250" fill="none" stroke="url(#ring)" stroke-width="6"/>
      <circle cx="255" cy="255" r="235" fill="#0a1a22"/>
      <circle cx="255" cy="255" r="222" fill="none" stroke="#1d4456" stroke-width="5"/>
      <circle cx="255" cy="255" r="200" fill="url(#disc)"/>
    </svg>
    <div class="badge-title">
      <span class="title-script">Youth</span>
      <span class="title-block">GROUP</span>
    </div>

    <p class="schedule">SUNDAYS, <span class="time">6-8PM</span></p>
    <div class="start-tab">BEGINNING</div>
    <div class="start-date">
      <span class="start-day">14<sup>TH</sup></span>
      <span class="start-month">APRIL</span>
    </div>

    <p class="location-label"><span>LOCATION:</span></p>
    <p class="location-box"><span class="venue">Marlowe's -</span> 4219 Quarry Fern Ave N, Keizer, 97318</p>

    <p class="extras-label">THERE WILL BE</p>
    <ul class="extras">
      <li class="navy">DINNER</li>
      <li class="brown">FRIENDS</li>
      <li class="navy">GAMES</li>
      <li class="brown">MESSAGE</li>
    </ul>
  </article>
</div>
</body>
</html>
```